Web Page Design for Major Airline Consolidator

We need a new design for an airline consolidator based out of NY. We'd really like to get the design as quickly as possible.

Here is a *very* rough mockup of what the site could look like, along with 3 main competitor's sites. Needless to say, they want a design that looks much better than their competitors. Please note that the mockup is an idea only, feel free to enhance / improve upon it.

Mockup - https://plankrafe.com/tvorel/KQPMzaLu

Competitors:
- http://www.brellintour.com/
- http://www.skorvatix.com/home2.html
- https://www.dulmerok.com/index.php

Target Market(s)

target markets are identified in the mockup

Industry/Entity Type

Airline

Number of Pages Required

1 page

Requirements
Must have
• need space on the left side for a travel request form which is missing in the mockup. Form should have standard air booking fields (to, from, date arrival & departure, travel class, etc).

```html
<!DOCTYPE html>
<html lang="en">
<head>
<meta charset="utf-8">
<title>Halvern Tours – Airline Consolidator</title>
<link href="https://fonts.googleapis.com/css2?family=Open+Sans:ital,wght@0,400;0,600;0,700;1,400&display=swap" rel="stylesheet">
<style>
:root{
  --orange:#f7941d;
  --orange-dark:#e07f0a;
  --ink:#2b2b2b;
  --text:#555;
  --muted:#888;
  --nav:#3a3a3a;
  --panel:#efefef;
  --line:#dcdcdc;
  --white:#fff;
  --footer:#4a4a4a;
}
*{box-sizing:border-box;margin:0;padding:0}
html,body{width:1200px;height:5393px;overflow:hidden}
body{font-family:"Open Sans",Arial,sans-serif;color:var(--text);background:var(--white);font-size:13px;line-height:1.5}
a{color:inherit;text-decoration:none}
.wrap{width:1050px;margin:0 auto;position:relative}
.btn{display:inline-block;background:var(--orange);color:var(--white);font-weight:600;font-size:12px;text-transform:uppercase;padding:8px 22px;letter-spacing:.5px}
.btn.grey{background:#777}
.section-title{text-align:center;font-size:28px;font-weight:600;color:var(--ink);text-transform:uppercase;letter-spacing:.5px}
.section-intro{text-align:center;font-size:12px;color:var(--muted);width:700px;margin:18px auto 0}
.photo{display:block}

/* header */
.site-header{height:62px}
.site-header .wrap{height:62px;display:flex;align-items:center;justify-content:space-between}
.brand{display:flex;align-items:center;gap:10px}
.brand-mark{width:30px;height:30px;background:var(--nav)}
.brand-name{font-size:24px;font-weight:600;color:var(--nav);line-height:1}
.brand-tag{font-size:10px;color:var(--muted);display:block;margin-top:3px}
.header-tools{text-align:right;font-size:11px;color:var(--muted)}
.search{display:inline-flex;border:1px solid var(--line);width:170px;height:24px;align-items:center;justify-content:space-between;padding:0 6px;font-size:11px}
.search-go{width:22px;height:24px;background:var(--orange);margin-left:4px;display:inline-block;vertical-align:top}
.account{margin-top:4px}
.main-nav{height:34px;background:var(--nav)}
.main-nav ul{list-style:none;display:flex;height:34px;width:1200px}
.main-nav li{color:var(--white);font-size:11px;font-weight:600;text-transform:uppercase;padding:0 17px;line-height:34px}
.main-nav li.active{background:var(--orange)}

/* hero */
.hero{height:964px;position:relative;background:linear-gradient(180deg,#6d8499 0%,#9fb2c3 35%,#c9d3da 58%,#7a8087 75%,#3d4146 100%)}
.plan-travel{position:absolute;left:0;right:0;top:620px;height:300px;background:rgba(40,40,40,.82);padding:28px 75px}
.plan-title{color:var(--orange);font-size:18px;font-weight:600}
.trip-type{display:flex;gap:30px;color:var(--white);font-size:12px;margin:12px 0 20px}
.trip-type span::before{content:"";display:inline-block;width:10px;height:10px;border-radius:50%;border:1px solid var(--white);margin-right:6px;vertical-align:-1px}
.trip-type span.on::before{background:var(--orange);border-color:var(--orange)}
.form-row{display:grid;grid-template-columns:repeat(4,1fr);gap:28px;margin-bottom:22px}
.field label{display:block;color:var(--white);font-size:11px;margin-bottom:5px}
.field .input{height:32px;background:var(--white);font-size:12px;color:var(--muted);padding:7px 10px}
.find-btn{height:32px;background:var(--orange);color:var(--white);font-weight:700;text-align:center;line-height:32px;margin-top:22px}

/* welcome */
.welcome{margin:100px 75px 0;height:500px;background:var(--panel);padding:50px 85px}
.welcome h1{text-align:center;font-size:28px;font-weight:600;color:var(--ink)}
.welcome .sub{text-align:center;font-size:16px;color:var(--ink);margin-top:8px}
.welcome-body{display:flex;justify-content:space-between;margin-top:50px}
.perks{list-style:none}
.perks li{font-size:14px;color:var(--ink);margin-bottom:22px;padding-left:22px;position:relative}
.perks li::before{content:"";position:absolute;left:0;top:7px;width:8px;height:8px;background:var(--orange)}
.signin{width:360px}
.signin p{font-size:14px;color:var(--ink);margin-bottom:18px}
.signin-box{background:var(--orange);padding:22px}
.signin-box .input{height:30px;background:var(--white);margin-bottom:12px;font-size:12px;color:var(--muted);padding:6px 10px;width:220px}
.signin-box .go{display:inline-block;background:var(--white);color:var(--ink);font-size:11px;font-weight:600;padding:5px 14px}

/* agents */
.agents{margin-top:190px}
.agent-cards{display:flex;gap:50px;margin-top:60px}
.agent-card{width:316px;background:var(--panel);height:510px}
.agent-card .photo{height:230px}
.agent-card .body{padding:18px 30px}
.agent-card h3{color:var(--orange);font-size:17px;font-weight:600;text-align:center}
.agent-card .lead{text-align:center;color:var(--ink);font-size:13px;margin-bottom:12px}
.agent-card ul{list-style:none;font-size:12px;margin-bottom:20px}
.agent-card li{padding-left:14px;position:relative;margin-bottom:4px}
.agent-card li::before{content:"";position:absolute;left:0;top:7px;width:5px;height:5px;background:var(--ink)}
.agent-card .btn{display:block;width:120px;margin:0 auto;text-align:center}

/* about */
.about{margin:100px 75px 0;height:540px;background:var(--panel);padding:45px 60px}
.about-grid{display:flex;gap:40px;margin-top:40px}
.about-left{flex:1}
.quote{display:flex;gap:24px;align-items:center}
.avatar{width:90px;height:90px;border-radius:50%;flex:none;background:radial-gradient(circle at 50% 40%,#bfc4c9,#6b7178)}
.quote blockquote{color:var(--orange);font-style:italic;font-size:15px}
.quote cite{display:block;font-style:normal;color:var(--ink);font-size:12px;margin-top:8px}
.about-left p.copy{font-size:12px;margin-top:24px}
.team{width:300px;border-left:1px solid var(--line);padding-left:30px}
.member{display:flex;gap:16px;align-items:center;margin-bottom:22px}
.member .avatar{width:58px;height:58px}
.member strong{display:block;color:var(--ink);font-size:12px;font-weight:600}
.member span{font-size:11px}

/* divisions */
.divisions{margin-top:130px}
.division-cards{display:flex;gap:60px;margin-top:60px}
.division{display:flex;gap:26px;width:495px;height:220px}
.division .photo{width:230px;flex:none}
.division h3{color:var(--orange);font-size:14px;font-weight:700;text-transform:uppercase;margin-top:10px}
.division p{font-size:12px;margin:8px 0 14px}
.division .more{font-size:11px;font-weight:600;color:var(--ink);border-bottom:1px solid var(--ink)}

/* business */
.business{margin:70px 75px 0;height:590px;background:var(--panel);padding:55px 60px;text-align:center}
.business h2{font-size:26px;font-weight:600;color:var(--ink)}
.business .sub{font-size:17px;color:var(--ink);margin-top:28px}
.benefits{display:flex;justify-content:space-between;margin:60px 20px 50px}
.benefit{width:190px}
.benefit svg{width:40px;height:40px;margin-bottom:12px}
.benefit p{font-size:12px}

/* deals */
.deals{margin-top:100px}
.deal-tabs{display:flex;gap:10px;margin-top:55px}
.deal-tabs span{flex:1;text-align:center;font-size:13px;font-weight:600;text-transform:uppercase;color:var(--muted);border-bottom:3px solid var(--line);padding:8px 0}
.deal-tabs span.active{background:var(--orange);color:var(--white);border-color:var(--orange)}
.deal-cards{display:flex;gap:50px;margin-top:30px}
.deal{width:316px;text-align:center}
.deal .photo{height:170px}
.deal h3{font-size:18px;font-weight:700;color:var(--ink);margin-top:14px}
.deal p{font-size:12px;margin:6px 20px 12px}
.deal .btn{padding:6px 18px}
.deals-more{text-align:right;font-size:12px;font-weight:600;color:var(--ink);margin-top:18px}

/* footer */
.site-footer{position:absolute;left:0;right:0;top:5150px;height:243px;background:var(--footer);color:#ddd}
.site-footer .wrap{display:flex;justify-content:space-between;padding-top:38px}
.site-footer .brand-name{color:var(--white)}
.site-footer .brand-mark{background:var(--white)}
.contact{font-size:11px;margin-top:16px;line-height:1.7}
.enews{width:300px;font-size:12px}
.enews .input{height:26px;background:var(--white);margin:10px 0;width:220px}
.enews .btn{padding:5px 14px;font-size:11px}
.trusted h4{color:var(--white);font-size:14px;font-weight:600;margin-bottom:14px}
.badges{display:flex;gap:14px}
.badges span{width:56px;height:40px;background:#777;display:block}
</style>
</head>
<body>

<header class="site-header">
  <div class="wrap">
    <div class="brand">
      <span class="brand-mark"></span>
      <div><span class="brand-name">Halvern Tours</span><span class="brand-tag">The Professional's Choice since 1974</span></div>
    </div>
    <div class="header-tools">
      <div><span class="search">Looking for...</span><span class="search-go"></span></div>
      <div class="account">My Account &nbsp;|&nbsp; Sign Up</div>
    </div>
  </div>
</header>
<nav class="main-nav">
  <ul>
    <li class="active">Home</li><li>About Halvern</li><li>Travel Agents</li><li>Religious &amp; Group Travel</li><li>Corporate Concierge</li><li>Book Airfares</li><li>Dept Sections</li><li>Restricted Area</li>
  </ul>
</nav>

<section class="hero" role="img" aria-label="Photo of a passenger jet taking off over a runway under a cloudy sky">
  <form class="plan-travel">
    <div class="plan-title">Plan Your Travel</div>
    <div class="trip-type"><span class="on">Round trip</span><span>One way</span><span>Multi city</span></div>
    <div class="form-row">
      <div class="field"><label>Leaving From</label><div class="input">New York</div></div>
      <div class="field"><label>Going To</label><div class="input">City or airport</div></div>
      <div class="field"><label>Departure</label><div class="input">mm/dd/yyyy</div></div>
      <div class="field"><label>Return</label><div class="input">mm/dd/yyyy</div></div>
    </div>
    <div class="form-row">
      <div class="field"><label>Travel Class</label><div class="input">Economy</div></div>
      <div class="field"><label>Adults</label><div class="input">1</div></div>
      <div class="field"><label>Children</label><div class="input">0</div></div>
      <div class="find-btn">FIND IT</div>
    </div>
  </form>
</section>

<section class="welcome">
  <h1>WELCOME TO HALVERN TOURS</h1>
  <div class="sub">More Than Just Airline Consolidation</div>
  <div class="welcome-body">
    <ul class="perks">
      <li>We're here for your clients!</li>
      <li>Over 40 years in business</li>
      <li>Locations across the USA</li>
      <li>50+ air carriers</li>
      <li>Worldwide – Europe &amp; Middle East travel</li>
    </ul>
    <div class="signin">
      <p>Sign in to Halvern Tours and experience in a whole new way</p>
      <div class="signin-box">
        <div class="input">Username</div>
        <div class="input">Password</div>
        <span class="go">GET STARTED NOW</span>
      </div>
    </div>
  </div>
</section>

<section class="agents wrap">
  <h2 class="section-title">Airline Consolidator for Travel Agents</h2>
  <p class="section-intro">We offer agents net fares, fast ticketing and friendly support on every route we serve. Our team works with you to grow sales, keep clients happy and save time on every single booking.</p>
  <div class="agent-cards">
    <article class="agent-card">
      <div class="photo" role="img" aria-label="Photo of a city skyline at dusk" style="background:linear-gradient(180deg,#3f5e86,#7f93a8)"></div>
      <div class="body">
        <h3>Home Based Travel Agents</h3>
        <div class="lead">Find your way to financial freedom</div>
        <ul><li>Start from home with net fares</li><li>Get steady support and training</li><li>Earn more per sale</li></ul>
        <a class="btn">Join Now</a>
      </div>
    </article>
    <article class="agent-card">
      <div class="photo" role="img" aria-label="Photo of office towers against a grey sky" style="background:linear-gradient(180deg,#8d9296,#5f6468)"></div>
      <div class="body">
        <h3>Small Travel Agencies</h3>
        <div class="lead">Accelerate your growth!</div>
        <ul><li>Access to net fares on most carriers</li><li>Fast ticketing and helpful staff</li><li>Tools to compete with larger firms</li></ul>
        <a class="btn grey">Join Now</a>
      </div>
    </article>
    <article class="agent-card">
      <div class="photo" role="img" aria-label="Photo of a tall glass tower at sunset" style="background:linear-gradient(180deg,#8a7a66,#4f4d4a)"></div>
      <div class="body">
        <h3>Corporate Travel Agencies</h3>
        <div class="lead">Earn &amp; serve higher value clients</div>
        <ul><li>Special fares for business class</li><li>Flexible rules for busy travelers</li><li>Dedicated account managers</li></ul>
        <a class="btn grey">Join Now</a>
      </div>
    </article>
  </div>
</section>

<section class="about">
  <h2 class="section-title">About Us</h2>
  <p class="section-intro">Since 1974 our New York team has helped agents and firms find better fares. We know the routes, the rules and the people who make travel work for your clients.</p>
  <div class="about-grid">
    <div class="about-left">
      <div class="quote">
        <div class="avatar" role="img" aria-label="Portrait photo of the company president"></div>
        <blockquote>"Great airfares are only the beginning; our real work is the service and care that travel clients feel on every trip."<cite>Mr. Dorian Veck &nbsp;·&nbsp; President &amp; CEO</cite></blockquote>
      </div>
      <p class="copy">Halvern Tours was founded with a simple idea: give agents the tools and fares they need to win. Today we work with more than fifty carriers, offer group and religious travel, and serve corporate clients across the USA, Europe and the Middle East.</p>
    </div>
    <div class="team">
      <div class="member"><div class="avatar" role="img" aria-label="Portrait photo of a team member"></div><div><strong>Sales Desk &nbsp;·&nbsp; Ext 10</strong><span>Fares and group quotes for agents</span></div></div>
      <div class="member"><div class="avatar" role="img" aria-label="Portrait photo of a team member"></div><div><strong>Ticketing &nbsp;·&nbsp; Ext 20</strong><span>Issue, change and refund tickets</span></div></div>
      <div class="member"><div class="avatar" role="img" aria-label="Portrait photo of a team member"></div><div><strong>Support &nbsp;·&nbsp; Ext 30</strong><span>Help with travel plans and advice</span></div></div>
    </div>
  </div>
</section>

<section class="divisions wrap">
  <h2 class="section-title">Our Divisions</h2>
  <p class="section-intro">From scheduled flights to private aviation, each division brings focus and care to a different kind of traveler and trip.</p>
  <div class="division-cards">
    <article class="division">
      <div class="photo" role="img" aria-label="Photo of a jet airliner parked at a gate" style="background:linear-gradient(180deg,#c8cdd2,#7d8186)"></div>
      <div><h3>Scheduled Services</h3><p>Net fares on major carriers with quick ticketing and support for agents of every size.</p><a class="more">VIEW MORE</a></div>
    </article>
    <article class="division">
      <div class="photo" role="img" aria-label="Photo of a private business jet at sunset" style="background:linear-gradient(180deg,#d9a85c,#5a4a3a)"></div>
      <div><h3>Business Aviation</h3><p>Charter and private flights for executives who need speed, comfort and full control of time.</p><a class="more">VIEW MORE</a></div>
    </article>
  </div>
</section>

<section class="business">
  <h2>AIRLINE CONSOLIDATORS FOR BUSINESSES &amp; CORPORATIONS</h2>
  <div class="sub">Tired of Travel Headaches? Make Business Travel EASY!</div>
  <div class="benefits">
    <div class="benefit">
      <svg viewBox="0 0 40 40"><rect x="4" y="18" width="7" height="16" fill="#f7941d"/><path d="M14 18 L21 5 Q25 5 24 12 L23 16 L34 16 Q37 17 36 21 L33 33 Q32 35 29 35 L14 35 Z" fill="#f7941d"/></svg>
      <p>Certified customer service, our staff has 200 agents and travel consultants</p>
    </div>
    <div class="benefit">
      <svg viewBox="0 0 40 40"><circle cx="20" cy="20" r="15" fill="none" stroke="#f7941d" stroke-width="3"/><path d="M20 10 V30 M25 14 H17 Q14 14 14 17 Q14 20 17 20 H23 Q26 20 26 23 Q26 26 23 26 H15" fill="none" stroke="#f7941d" stroke-width="2.5"/></svg>
      <p>Always available, easy to book and save more time</p>
    </div>
    <div class="benefit">
      <svg viewBox="0 0 40 40"><circle cx="20" cy="20" r="15" fill="none" stroke="#f7941d" stroke-width="3"/><path d="M20 11 V20 L27 24" fill="none" stroke="#f7941d" stroke-width="3"/></svg>
      <p>Save more by going direct to the consolidator</p>
    </div>
    <div class="benefit">
      <svg viewBox="0 0 40 40"><path d="M4 22 L16 20 L10 6 L15 6 L24 19 L34 18 Q38 20 34 22 L24 21 L15 34 L10 34 L16 22 L4 21 Z" fill="#f7941d"/></svg>
      <p>Your best interests are ours</p>
    </div>
  </div>
  <a class="btn" style="text-transform:none;padding:9px 30px">Experience the difference of Halvern</a>
</section>

<section class="deals wrap">
  <h2 class="section-title">Find Your Perfect Travel Deals</h2>
  <p class="section-intro">Browse group, individual and specialty rates built for agents. Each fare is hand picked by our team and updated often so you can book with confidence.</p>
  <div class="deal-tabs"><span class="active">Group Travel</span><span>Individual Trips</span><span>Specialty Travel</span></div>
  <div class="deal-cards">
    <article class="deal">
      <div class="photo" role="img" aria-label="Photo of pilgrims gathered around a holy site" style="background:linear-gradient(180deg,#8d8f93,#3e3f43)"></div>
      <h3>HAJJ Group Travel Rates</h3><p>Group fares and full support for pilgrims traveling together.</p><a class="btn">Contact Us</a>
    </article>
    <article class="deal">
      <div class="photo" role="img" aria-label="Photo of a windmill on a hill at dusk" style="background:linear-gradient(180deg,#9a7f62,#4a4038)"></div>
      <h3>Missionary Travel Rates</h3><p>Flexible fares for missionaries and church groups worldwide.</p><a class="btn">Contact Us</a>
    </article>
    <article class="deal">
      <div class="photo" role="img" aria-label="Photo of a crowded mosque courtyard" style="background:linear-gradient(180deg,#7b7c80,#2e2f33)"></div>
      <h3>Umra Travel Rates</h3><p>Year round Umra fares with group and family options.</p><a class="btn">Contact Us</a>
    </article>
  </div>
  <div class="deals-more">More</div>
</section>

<footer class="site-footer">
  <div class="wrap">
    <div>
      <div class="brand"><span class="brand-mark"></span><span class="brand-name">Halvern Tours</span></div>
      <div class="contact">
        410 Harlow Avenue, Suite 12<br>
        New York, NY 10099<br>
        Tel: +1 555 014 2290<br>
        Email: desk@halverntours.example
      </div>
    </div>
    <div class="enews">
      Sign up for eNews<br>Get fare deals and news sent to your inbox
      <div class="input"></div>
      <a class="btn">Sign Up</a>
    </div>
    <div class="trusted">
      <h4>Trusted Members</h4>
      <div class="badges"><span></span><span></span><span></span></div>
    </div>
  </div>
</footer>

</body>
</html>
```